Pet sitting Business needs a website

We need a website that shows our services and prices. Shows our love of animals but also our professionalism. want a gallery, about, blog, services, links to fb and instagram accounts, newsletter archive. want it to be easy to access and wonderful to navigate. want the domain to be Birchfordpawhaven.com
take any info from FB site www.facebook.com/birchfordpawhaven
I would like it to fit square space platform

Target Market(s)

upscale area, responsible pet owners,

Industry/Entity Type

Pet Care

Coding

Coded - Design and coding required

Number of Pages Required

5+ page

Font styles to use
Sans Serif

Requirements
Must have
• (square space platform)
• Menu
• photo gallery
• about us
• services
• policies
• monthly newsletter
• unavailable dates
• Introduction (welcome)
• payment methods
• Daily updates
• testimonials (use from fb site)
Should not have
• stock photos

```html
<!DOCTYPE html>
<html lang="en">
<head>
<meta charset="utf-8">
<title>Birchford Paw Haven</title>
<link href="https://fonts.googleapis.com/css2?family=Dancing+Script:wght@500;700&family=Open+Sans:wght@400;600;700;800&display=swap" rel="stylesheet">
<style>
:root{
  --blue:#0a78ad;
  --blue-dark:#06659a;
  --yellow:#e4a512;
  --yellow-light:#f0b62a;
  --slate:#575757;
  --ink:#222;
  --muted:#666;
  --line:#ddd;
  --white:#fff;
  --social-a:#6d62c9;
  --social-b:#1ea3e0;
  --social-c:#e04c3a;
  --social-d:#2a4a8c;
}
*{box-sizing:border-box;margin:0;padding:0}
html,body{width:1200px;height:2927px;overflow:hidden}
body{position:relative;font-family:"Open Sans",Arial,sans-serif;color:var(--ink);background:var(--white)}
.abs{position:absolute}
.script{font-family:"Dancing Script",cursive}

/* header */
.site-header{position:absolute;left:0;top:0;width:1200px;height:129px;background:var(--white)}
.brand{position:absolute;left:133px;top:34px;display:flex;align-items:center;gap:12px}
.brand-dot{width:46px;height:46px;border-radius:50%;background:var(--yellow);flex:none}
.brand-name{font-weight:700;font-size:20px;color:var(--yellow);line-height:1.15;width:140px}
.signup-label{left:558px;top:32px;font-size:12px;font-weight:700;color:#555}
.signup-field{left:558px;top:60px;width:222px;height:40px;border:1px solid #ccc;border-right:0;font-size:12px;color:#888;padding:11px 0 0 18px;display:flex;gap:8px}
.signup-go{left:780px;top:60px;width:36px;height:40px;background:var(--blue)}
.follow-label{left:868px;top:23px;font-size:10px;color:#777}
.socials{display:flex;gap:5px}
.socials span{width:22px;height:22px;display:block;border-radius:2px}
.s1{background:var(--social-a)}.s2{background:var(--social-b)}.s3{background:var(--social-c)}.s4{background:var(--social-d)}
.header-socials{left:963px;top:18px}
.phone-ring{left:864px;top:60px;width:38px;height:38px;border:2px solid var(--blue);border-radius:50%}
.join{left:913px;top:60px;font-size:12px;font-weight:700;color:#888}
.phone{left:913px;top:77px;font-size:22px;font-weight:800;color:var(--yellow)}

/* nav */
.main-nav{position:absolute;left:0;top:129px;width:1200px;height:37px;background:var(--blue);border-bottom:3px solid var(--blue-dark)}
.main-nav ul{list-style:none;display:flex;justify-content:space-between;position:absolute;left:133px;top:0;width:934px;height:34px}
.main-nav li{font-size:12px;font-weight:700;color:var(--white);line-height:34px}
.main-nav li.active{background:var(--yellow);padding:0 12px}

/* hero */
.hero{position:absolute;left:0;top:166px;width:1200px;height:430px;
  background:linear-gradient(90deg,#3d4a2c 0%,#5b5a40 18%,#6e4e34 36%,#9a6b48 46%,#e6ddd2 58%,#b58258 70%,#7a5234 80%,#4d6a2e 92%,#3f5a28 100%)}
.hero-title{left:136px;top:130px;width:340px;font-size:46px;font-weight:500;color:var(--white);line-height:55px;text-shadow:0 2px 6px rgba(0,0,0,.35)}
.dots{left:548px;top:394px;display:flex;gap:14px}
.dots span{width:9px;height:9px;border-radius:50%;background:var(--white);display:block}
.hero-wave{position:absolute;left:0;top:536px;width:1200px}

/* services */
.services{position:absolute;left:0;top:585px;width:1200px;height:597px;background:linear-gradient(180deg,#0d7bb2,#066ba1)}
.section-title{position:absolute;width:100%;text-align:center;font-family:"Dancing Script",cursive;font-weight:700;font-size:36px}
.title-rule{position:absolute;left:50%;width:170px;margin-left:-85px;height:2px}
.tile{position:absolute;width:302px;height:218px;overflow:hidden;box-shadow:0 3px 8px rgba(0,0,0,.3)}
.tile-label{position:absolute;left:12px;bottom:8px;font-family:"Dancing Script",cursive;font-weight:700;font-size:25px;color:var(--yellow-light)}
.tile-price{position:absolute;right:10px;bottom:10px;font-size:19px;font-weight:700;color:var(--white)}
.tile-shade{position:absolute;left:0;bottom:0;width:100%;height:70px;background:linear-gradient(transparent,rgba(0,0,0,.6))}

/* welcome */
.welcome-title{left:133px;top:1222px;font-size:34px;font-weight:700;color:var(--blue)}
.welcome-lead{left:133px;top:1280px;width:300px;font-size:12.5px;line-height:21px;color:#222}
.welcome-body{left:133px;top:1332px;width:238px;font-size:12.5px;line-height:21px;color:#555;text-align:justify}
.welcome-art{left:386px;top:1282px;width:282px;height:256px;border-radius:50% 50% 8px 8px;background:linear-gradient(90deg,#1d7fb4 0%,#1d7fb4 30%,#e4a512 60%,#e4a512 100%);opacity:.9}
.btn-more{left:136px;top:1535px;width:120px;height:40px;background:var(--blue);color:var(--white);font-size:12px;font-weight:700;padding:12px 0 0 18px}
.news{position:absolute;left:691px;top:1206px;width:376px;height:406px;background:var(--slate)}
.news-title{left:28px;top:14px;font-size:30px;font-weight:700;color:var(--yellow-light)}
.news-item{position:absolute;left:28px;width:330px;height:80px}
.news-thumb{position:absolute;left:0;top:0;width:116px;height:80px}
.news-date{position:absolute;left:136px;top:0;font-size:10px;color:#ccc}
.news-head{position:absolute;left:136px;top:16px;width:200px;font-size:12px;font-weight:700;color:var(--white);line-height:17px}
.news-sub{position:absolute;left:136px;top:54px;width:200px;font-size:10px;color:#bbb;line-height:14px}

/* gallery */
.gallery{position:absolute;left:0;top:1637px;width:1200px;height:513px;background:linear-gradient(120deg,#e8a914,#d99a0c 50%,#eab22a)}
.gallery-main{position:absolute;left:133px;top:113px;width:560px;height:363px;background:linear-gradient(100deg,#2b2530 0%,#4a3e48 30%,#f1eee8 52%,#cfc7bc 70%,#6a5a50 100%)}
.arrow-box{position:absolute;width:44px;height:44px}
.thumb{position:absolute;width:176px;height:117px}

/* testimonials */
.card{position:absolute;top:2273px;width:456px;height:273px;border:1px solid var(--line);background:var(--white);box-shadow:0 6px 8px -4px rgba(0,0,0,.15)}
.quote-mark{position:absolute;font-family:Georgia,serif;font-size:60px;color:#ccc;line-height:1}
.quote-text{position:absolute;left:76px;top:46px;width:314px;font-size:12px;line-height:24px;color:#666;text-align:justify}
.card-rule{position:absolute;left:76px;top:189px;width:314px;height:1px;background:var(--line)}
.avatar{position:absolute;left:76px;top:206px;width:38px;height:38px;border-radius:50%;background:linear-gradient(135deg,#c9a68a,#5a6a78)}
.who{position:absolute;left:130px;top:210px;font-size:10px;font-weight:700;color:var(--blue)}
.where{position:absolute;left:130px;top:226px;font-size:10px;color:#777}
.circle-arrow{position:absolute;top:2381px;width:48px;height:48px;border-radius:50%;background:#555}

/* footer */
.site-footer{position:absolute;left:0;top:2595px;width:1200px;height:293px;background:var(--blue)}
.footer-brand{left:133px;top:68px;display:flex;align-items:center;gap:12px}
.footer-brand .brand-dot{background:var(--white)}
.footer-brand .brand-name{color:var(--white)}
.footer-rule{left:133px;top:191px;width:378px;height:1px;background:rgba(255,255,255,.4)}
.footer-follow{left:166px;top:221px;font-size:11px;font-weight:700;color:var(--white);letter-spacing:1px}
.footer-socials{left:293px;top:216px;gap:14px}
.footer-col h4{font-size:12px;font-weight:700;color:var(--white);margin-bottom:14px}
.footer-col p,.footer-col li{font-size:11px;line-height:17px;color:#e6f2f9;list-style:none}
.footer-field{left:784px;top:74px;width:283px;height:47px;background:var(--white);font-size:12px;color:#777;padding:15px 0 0 18px;display:flex;gap:10px}
.footer-btn{left:784px;top:131px;width:283px;height:49px;background:var(--yellow);color:var(--white);font-size:20px;font-weight:800;text-align:center;line-height:49px}
.copyright{position:absolute;left:0;top:2888px;width:1200px;height:39px;background:#0a6c9e;color:#dcecf5;font-size:11px;text-align:center;line-height:39px}
</style>
</head>
<body>

<header class="site-header">
  <div class="brand"><span class="brand-dot"></span><span class="brand-name">Birchford Paw Haven</span></div>
  <div class="abs signup-label">NEWSLETTER SIGNUP!</div>
  <div class="abs signup-field">
    <svg width="12" height="10" viewBox="0 0 12 10"><rect x=".5" y=".5" width="11" height="9" fill="none" stroke="#888"/><path d="M.5 .5l5.5 5 5.5-5" fill="none" stroke="#888"/></svg>
    <span>E mail id</span>
  </div>
  <div class="abs signup-go">
    <svg width="36" height="40" viewBox="0 0 36 40"><path d="M15 14l6 6-6 6" stroke="#fff" stroke-width="2.5" fill="none"/></svg>
  </div>
  <div class="abs follow-label">FOLLOW US ON :</div>
  <div class="abs socials header-socials"><span class="s1"></span><span class="s2"></span><span class="s3"></span><span class="s4"></span></div>
  <div class="abs phone-ring">
    <svg width="34" height="34" viewBox="0 0 34 34"><path d="M12 10c1-1 2-1 3 0l2 3c.5 1 0 2-1 2.5 1 2 2.5 3.5 4.5 4.5.5-1 1.5-1.5 2.5-1l3 2c1 1 1 2 0 3-3 3-7 1-11-3s-6-8-3-11z" fill="#0a78ad"/></svg>
  </div>
  <div class="abs join">JOIN THE CLUB TODAY</div>
  <div class="abs phone">312 - 555 - 0148</div>
</header>

<nav class="main-nav">
  <ul>
    <li class="active">HOME</li><li>ABOUT US</li><li>SERVICES</li><li>POLICIES</li><li>PHOTO GALLERY</li><li>UNAVAILABLE DATES</li><li>NEWSLETTER</li><li>CONTACT US</li>
  </ul>
</nav>

<section class="hero" role="img" aria-label="Close-up photo of a smiling spaniel dog">
  <h1 class="abs hero-title script">Where kisses and hugs are my speciality</h1>
  <div class="abs dots"><span></span><span></span><span></span><span></span><span></span></div>
</section>
<svg class="hero-wave" height="60" viewBox="0 0 1200 60" preserveAspectRatio="none">
  <path d="M0 60 L0 48 Q300 20 600 30 T1200 10 L1200 60Z" fill="#0d7bb2"/>
  <path d="M0 48 Q300 20 600 30 T1200 10" stroke="#e4a512" stroke-width="3" fill="none"/>
</svg>

<section class="services">
  <h2 class="section-title" style="top:50px;color:var(--white)">Our Services</h2>
  <div class="title-rule" style="top:110px;background:var(--yellow)"></div>

  <div class="tile" style="left:133px;top:123px;background:linear-gradient(120deg,#3f6a2c 0%,#c89a80 40%,#e8e2da 55%,#5a4a3a 75%,#4a7a34 100%)" role="img" aria-label="Sitter holding a pug"><div class="tile-shade"></div><span class="tile-label">Daily Visit</span><span class="tile-price">$25.00</span></div>
  <div class="tile" style="left:449px;top:123px;background:linear-gradient(120deg,#3a2e2a 0%,#a07058 35%,#d8b49a 60%,#9ab0c0 100%)" role="img" aria-label="Sitter with a small dog"><div class="tile-shade"></div><span class="tile-label">Potty Visit</span><span class="tile-price">$10.00</span></div>
  <div class="tile" style="left:763px;top:123px;background:linear-gradient(160deg,#2e4a20 0%,#5a7a38 40%,#b88e60 60%,#6e9a40 100%)" role="img" aria-label="Dog standing in a park"><div class="tile-shade"></div><span class="tile-label">Dog Park</span><span class="tile-price">$40.00</span></div>
  <div class="tile" style="left:133px;top:352px;background:linear-gradient(120deg,#c8c8c0 0%,#8a8a84 40%,#1e1e20 60%,#a8a8a0 100%)" role="img" aria-label="Dog on a leash walk"><div class="tile-shade"></div><span class="tile-label">Just walks</span><span class="tile-price">$15.00</span></div>
  <div class="tile" style="left:449px;top:352px;background:linear-gradient(120deg,#1e2a3a 0%,#3a4e66 35%,#a06a48 55%,#2a3444 100%)" role="img" aria-label="Dog riding in a car"><div class="tile-shade"></div><span class="tile-label">Pet Taxi</span><span class="tile-price">$15.00</span></div>
  <div class="tile" style="left:763px;top:352px;background:linear-gradient(120deg,#7a5a44 0%,#c89a70 35%,#efe8e0 60%,#b8a898 100%)" role="img" aria-label="Dog receiving medication"><div class="tile-shade"></div><span class="tile-label">Medication</span><span class="tile-price">$5.00</span></div>
</section>

<section class="welcome">
  <h2 class="abs welcome-title script">Welcome to our site</h2>
  <p class="abs welcome-lead">Contrary to popular belief, Lorem Ipsum is not simply random text. It has roots in a piece.</p>
  <p class="abs welcome-body">There are many variations of passages of Lorem Ipsum available, but the majority have suffered alteration in some form, by injected humour, or randomised words which don't look even slightly believable. If you are going to use a passage of Lorem Ipsum, you need to be sure there isn't anything embarrassing hidden in the middle of text.</p>
  <div class="abs welcome-art" role="img" aria-label="Illustration of a blue cat and a yellow dog sitting together"></div>
  <div class="abs btn-more">READ MORE &#8250;</div>

  <aside class="news">
    <h3 class="abs news-title script">News &amp; Events</h3>
    <div class="news-item" style="top:76px"><div class="news-thumb" style="background:linear-gradient(135deg,#6a5a48,#e8e0d4 60%,#8a7458)" role="img" aria-label="Small white dog photo"></div><span class="news-date">May 22, 2016</span><span class="news-head">It's about that time again! Vacation season!!</span><span class="news-sub">We are gearing up again for a great year full of adventures.</span></div>
    <div class="news-item" style="top:186px"><div class="news-thumb" style="background:linear-gradient(135deg,#4a6a30,#2a2a28 50%,#e8e4dc 70%,#5a7a38)" role="img" aria-label="Dog on grass photo"></div><span class="news-date">May 22, 2016</span><span class="news-head">I AM TAKING 2 WEEKS OFF THIS SUMMER!!!!!!! GOING TO</span><span class="news-sub">We are gearing up again for a great year full of adventures.</span></div>
    <div class="news-item" style="top:296px"><div class="news-thumb" style="background:linear-gradient(135deg,#2a2220,#8a6048 50%,#3a3430)" role="img" aria-label="Photo of a graduate"></div><span class="news-date">May 22, 2016</span><span class="news-head">{THIS IS WHEN MY NEPHEW GRADUATES,DEPENDING...</span><span class="news-sub">We are gearing up again for a great year full of adventures.</span></div>
  </aside>
</section>

<section class="gallery">
  <h2 class="section-title" style="top:34px;color:#3a3a3a">Photo Gallery</h2>
  <div class="title-rule" style="top:94px;background:#3a3a3a"></div>
  <div class="gallery-main" role="img" aria-label="Sitter with a black and white cat on a staircase">
    <div class="arrow-box" style="left:0;top:160px;background:rgba(200,200,200,.85)"><svg width="44" height="44" viewBox="0 0 44 44"><path d="M25 15l-7 7 7 7" stroke="#333" stroke-width="2.5" fill="none"/></svg></div>
    <div class="arrow-box" style="right:0;top:160px;background:rgba(255,255,255,.85)"><svg width="44" height="44" viewBox="0 0 44 44"><path d="M19 15l7 7-7 7" stroke="#333" stroke-width="2.5" fill="none"/></svg></div>
  </div>
  <div class="thumb" style="left:702px;top:113px;background:linear-gradient(135deg,#c89a80,#3a3230 50%,#5a6a3a)" role="img" aria-label="Sitter with a black dog"></div>
  <div class="thumb" style="left:891px;top:113px;background:linear-gradient(135deg,#e8e0d8,#c89a70 50%,#b86a30)" role="img" aria-label="Sitter with a ginger cat"></div>
  <div class="thumb" style="left:702px;top:236px;background:linear-gradient(135deg,#3a3a44,#c8905a 50%,#e8e2da)" role="img" aria-label="Dog portrait in a car"></div>
  <div class="thumb" style="left:891px;top:236px;background:linear-gradient(135deg,#4a6a2e,#c89a70 50%,#6a4a34)" role="img" aria-label="Sitter with a dog outdoors"></div>
  <div class="thumb" style="left:702px;top:359px;background:linear-gradient(135deg,#3e6a2a,#f0eee8 50%,#4a7a30)" role="img" aria-label="Dog on grass"></div>
  <div class="thumb" style="left:891px;top:359px;background:linear-gradient(135deg,#2a2626,#c8a088 50%,#d8d4cc)" role="img" aria-label="Sitter hugging a dog"></div>
</section>

<section class="testimonials">
  <h2 class="section-title" style="top:2184px;color:var(--blue)">Testimonials</h2>
  <div class="title-rule" style="top:2242px;background:var(--blue)"></div>

  <article class="card" style="left:133px">
    <span class="quote-mark" style="left:30px;top:28px">&ldquo;</span>
    <p class="quote-text">There are many variations of passages of Lorem Ipsum available, but the majority have suffered alteration in some form, by injected humour, or randomised words which don't look even slightly believable. If you are going to use a passage</p>
    <span class="quote-mark" style="left:136px;top:136px">&rdquo;</span>
    <div class="card-rule"></div><div class="avatar" role="img" aria-label="Reviewer portrait"></div>
    <span class="who">MARION ELLERY</span><span class="where">Australia</span>
  </article>
  <article class="card" style="left:611px">
    <span class="quote-mark" style="left:30px;top:28px">&ldquo;</span>
    <p class="quote-text">It is a long established fact that a reader will be distracted by the readable content of a page when looking at its layout. The point of using Lorem Ipsum is that it has a more-or-less normal distribution of letters, as opposed to using 'Content</p>
    <span class="quote-mark" style="left:170px;top:136px">&rdquo;</span>
    <div class="card-rule"></div><div class="avatar" role="img" aria-label="Reviewer portrait"></div>
    <span class="who">MARION ELLERY</span><span class="where">Australia</span>
  </article>
  <div class="circle-arrow" style="left:93px"><svg width="48" height="48" viewBox="0 0 48 48"><path d="M27 16l-8 8 8 8" stroke="#fff" stroke-width="2.5" fill="none"/></svg></div>
  <div class="circle-arrow" style="left:1059px"><svg width="48" height="48" viewBox="0 0 48 48"><path d="M21 16l8 8-8 8" stroke="#fff" stroke-width="2.5" fill="none"/></svg></div>
</section>

<footer class="site-footer">
  <div class="abs footer-brand"><span class="brand-dot"></span><span class="brand-name">Birchford Paw Haven</span></div>
  <div class="abs footer-rule"></div>
  <div class="abs footer-follow">FOLLOW US ON!</div>
  <div class="abs socials footer-socials"><span class="s4"></span><span class="s2"></span><span class="s3"></span><span class="s4"></span></div>

  <div class="abs footer-col" style="left:398px;top:48px">
    <h4>CONTACT US</h4>
    <p>48 Linden Row</p><p>Marlow, KS 66090</p><p>T : 1.800.555.0199</p><p>E : hello@birchfordpawhaven.com</p>
  </div>
  <div class="abs footer-col" style="left:603px;top:48px">
    <h4>MENU</h4>
    <ul><li>Home</li><li>Photo gallery</li><li>About us</li><li>Services</li><li>Policies</li><li>Monthly newsletter</li><li>Unavailable dates</li><li>Introduction (welcome)</li><li>Payment methods</li></ul>
  </div>
  <div class="abs footer-col" style="left:784px;top:48px"><h4>NEWSLETTTER SIGNUP!</h4></div>
  <div class="abs footer-field">
    <svg width="12" height="10" viewBox="0 0 12 10"><rect x=".5" y=".5" width="11" height="9" fill="none" stroke="#777"/><path d="M.5 .5l5.5 5 5.5-5" fill="none" stroke="#777"/></svg>
    <span>E mail id</span>
  </div>
  <div class="abs footer-btn">SIGNUP!</div>
</footer>
<div class="copyright">Copyrights @ 2016 All Rights Reserved</div>

</body>
</html>
```